Form Sculptors Business Card

Professional cosmetic surgery company, based in very exclusive area in London. High profiled clientele. Brand is very artistic, modern, state-of-the-art, safe. The best in the business. Celebrity clientele.

Form Sculptor’s of London is a brand serving a discriminating and exclusive clientele who value personal service that is both intimate and high end. Our clients choose Form Sculptors because of the relationships we share with all of our customers. The clients of Form Sculptors have an equal partnership between customers, and very experienced, highly qualified medical professionals. This together provides you with a professional service that keeps you looking good and feeling good. It is a relationship based on honesty, compassion, loyalty and respect.
Form Sculptor’s have provided services for internationally recognised celebrities, and other high profiled individuals.

The cards are used for networking at private, exclusive events with VIPs.

Target Market(s)

Professionals
Rich people

Industry/Entity Type

Professional Service

Contact Information for Business Card

Need double sided business card design for 4 people. Back of the business card needs to have contrast background to the front with butterfly watermark with services provided:
Hair Restoration surgery
Hair Loss treatments
Breast surgery
Rhinoplasty
Pulvix Liposuction
Fat Grafting
Lumaxin & Fillers

Front of the business card needs to be a nice satin black.
with following information:
Calvert Osterlund - name
Chief Executive - Job title

www.formsculptors-example.co.uk
calvert@formsculptors-example.co.uk
Phone: +44 (0)207 946 0321
Mobile: +44 (0)7700 900 147

The London Farrowmere Clinic
14 Farrowmere Lane | London | W1X 4QP
Off Quenby Street

All business cards have the same address, phone, website as Calvert's details.
Same details on the back of the business card as well.
The other cards have different name, job title, email, mobile number

Teodor Lunn - Name
Partner - Job Title
Former England International Cricketer - please include below job title

email: teodor@formsculptors-example.co.uk
mobile: +44(0)7700 900582

Dr Castello Vranesk - Name
Plastic Surgeon - Job Title
drvranesk@formsculptors-example.co.uk
No mobile number

Dr Ezra Tolquist FRCS (please put FRCS in small font) - Name
Hair Restoration Surgeon - Job Title
drtolquist@formsculptors-example.co.uk
No mobile number

Colors
cedeec
85abd2
0655a3

Requirements
Must have
• The logo needs to be in a metallic finish
• Text needs to be striking
• nice background
• butterfly watermark on the back

```html
<!DOCTYPE html>
<html lang="en">
<head>
<meta charset="utf-8">
<title>Form Sculptors Business Card</title>
<link rel="stylesheet" href="https://fonts.googleapis.com/css2?family=Arimo:wght@400;700&display=swap">
<style>
  :root {
    --page-bg: #e9e5df;
    --card-black: #050505;
    --card-white: #ffffff;
    --text-light: #f2f2f2;
    --text-soft: #d8d8d8;
    --band-gold: #f2a91c;
    --band-text: #1a1206;
    --brand-blue: #2f63b4;
    --brand-orange: #f08a1e;
    --service-blue: #2f5fb0;
    --heading-dark: #1b1b1b;
  }
  * { box-sizing: border-box; margin: 0; padding: 0; }
  html, body {
    width: 1200px; height: 870px; overflow: hidden;
    background: var(--page-bg);
    font-family: "Arimo", Arial, sans-serif;
  }
  .sheet {
    position: relative; width: 1200px; height: 870px;
    display: flex; justify-content: center; align-items: center; gap: 60px;
  }
  .card {
    position: relative; width: 440px; height: 700px; overflow: hidden;
    box-shadow: 0 6px 18px rgba(0,0,0,.18);
  }

  /* Front */
  .card-front { background: var(--card-black); color: var(--text-light); text-align: center; }
  .brand {
    position: absolute; top: 62px; left: 0; right: 0;
    display: flex; justify-content: center; align-items: center; gap: 14px;
  }
  .brand-dot { width: 22px; height: 22px; border-radius: 50%; background: var(--brand-orange); }
  .brand-name { font-size: 36px; font-weight: 400; letter-spacing: 1px; color: var(--brand-blue); }
  .clinic { position: absolute; top: 160px; left: 0; right: 0; font-size: 30px; font-weight: 400; line-height: 1.15; }
  .person { position: absolute; top: 252px; left: 0; right: 0; }
  .person-name { font-size: 29px; }
  .person-title { font-size: 20px; color: var(--text-soft); margin-top: 2px; }
  .person-mobile { font-size: 20px; color: var(--text-soft); margin-top: 6px; }
  .contact { position: absolute; top: 378px; left: 0; right: 0; font-size: 20px; line-height: 1.4; color: var(--text-soft); }
  .butterfly-art {
    position: absolute; left: 24px; bottom: 62px; width: 180px; height: 130px;
    background: linear-gradient(120deg, var(--brand-orange) 0%, #f6b13a 40%, #2a7fd0 70%, var(--brand-blue) 100%);
    border-radius: 40% 60% 10% 30%;
  }
  .web-band {
    position: absolute; left: 0; right: 0; bottom: 0; height: 62px;
    background: var(--band-gold); color: var(--band-text);
    display: flex; align-items: center; justify-content: flex-end; padding-right: 28px;
    font-size: 20px;
  }

  /* Back */
  .card-back { background: var(--card-white); }
  .watermark {
    position: absolute; left: 70px; top: 150px; width: 320px; height: 400px;
    background: radial-gradient(ellipse at 40% 35%, rgba(240,138,30,.16), rgba(240,138,30,0) 60%),
                radial-gradient(ellipse at 60% 70%, rgba(47,99,180,.16), rgba(47,99,180,0) 60%);
    border-radius: 50%;
  }
  .services { position: absolute; top: 245px; left: 0; right: 0; text-align: center; }
  .services-heading { font-size: 30px; font-weight: 400; color: var(--heading-dark); margin-bottom: 12px; }
  .services-list { list-style: none; font-size: 20px; line-height: 1.42; color: var(--service-blue); }
</style>
</head>
<body>
<main class="sheet">
  <section class="card card-front">
    <div class="brand">
      <span class="brand-dot"></span>
      <span class="brand-name">Form Sculptors</span>
    </div>
    <h1 class="clinic">The London Farrowmere<br>Clinic</h1>
    <div class="person">
      <p class="person-name">Calvert Osterlund</p>
      <p class="person-title">Chief Executive</p>
      <p class="person-mobile">+44 (0)7700 900 147</p>
    </div>
    <div class="contact">
      <p>+44 (0)207 946 0321</p>
      <p>calvert@formsculptors-example.co.uk</p>
      <p>14 Farrowmere Lane | London | W1X 4QP</p>
      <p>Off Quenby Street</p>
    </div>
    <div class="butterfly-art" role="img" aria-label="Orange and blue metallic butterfly illustration"></div>
    <div class="web-band">www.formsculptors-example.co.uk</div>
  </section>

  <section class="card card-back">
    <div class="watermark" role="img" aria-label="Faint orange and blue butterfly watermark"></div>
    <div class="services">
      <h2 class="services-heading">services</h2>
      <ul class="services-list">
        <li>Hair Restoration surgery</li>
        <li>Hair Loss treatments</li>
        <li>Breast surgery</li>
        <li>Rhinoplasty</li>
        <li>Pulvix Liposuction</li>
        <li>Fat Grafting</li>
        <li>Lumaxin &amp; Fillers</li>
      </ul>
    </div>
  </section>
</main>
</body>
</html>
```